Brisk Coatings business card for residential and commercial painting

A clean, professional design. Easy to read
Eye catching and elegant
Front could have some color variations
On the back of card I would like all black with signature logo

*Attached is my current business card and the items I want displayed

Contact Information for Business Card

Email, phone number, website, and owner name

Font styles to use
Serif

Requirements
Must have
• My logo with cool design and perhaps some paint splatter

```html
<!DOCTYPE html>
<html lang="en">
<head>
<meta charset="utf-8">
<title>Brisk Coatings – Business Card</title>
<link href="https://fonts.googleapis.com/css2?family=Roboto:wght@400;500;700&display=swap" rel="stylesheet">
<style>
  :root{
    --backdrop:#3b3b3d;
    --card:#1c1c1e;
    --emboss:#3a3a3d;
    --emboss-edge:#4a4a4e;
    --ink:#f2f2f2;
    --muted:#d8d8d8;
    --accent:#1e88d8;
  }
  *{box-sizing:border-box;margin:0;padding:0}
  html,body{width:799px;height:1200px;overflow:hidden}
  body{
    background:var(--backdrop);
    font-family:"Roboto",Arial,sans-serif;
    position:relative;
  }
  .card{
    position:absolute;
    left:80px;
    width:640px;
    height:366px;
    background:var(--card);
    border-radius:4px;
    box-shadow:0 18px 40px rgba(0,0,0,.45);
    overflow:hidden;
  }
  .card--front{top:120px}
  .card--back{top:714px}

  /* Front */
  .wordmark{
    display:flex;align-items:center;gap:14px;
    font-weight:700;text-transform:uppercase;letter-spacing:1px;
  }
  .wordmark__square{width:22px;height:22px;flex:none}
  .card--front .wordmark{
    position:absolute;left:0;right:0;top:132px;justify-content:center;
    font-size:50px;color:var(--emboss);
  }
  .card--front .wordmark__square{background:var(--emboss)}
  .front-url{
    position:absolute;left:0;right:0;top:206px;text-align:center;
    font-size:17px;font-weight:500;color:var(--ink);letter-spacing:.5px;
  }
  .front-url__name{color:var(--accent)}

  /* Back */
  .card--back .wordmark{
    position:absolute;right:40px;top:60px;
    font-size:36px;color:var(--ink);
  }
  .card--back .wordmark__square{width:18px;height:18px;background:var(--ink)}
  .owner{position:absolute;left:40px;top:150px}
  .owner__name{font-size:24px;font-weight:700;color:var(--accent)}
  .owner__role{font-size:15px;color:var(--ink);margin-top:4px}
  .sweep{position:absolute;left:0;top:0}
  .contacts{
    position:absolute;left:40px;top:228px;right:40px;
    display:flex;gap:22px;align-items:center;
    font-size:14px;color:var(--ink);
  }
  .contact{display:flex;align-items:center;gap:7px;white-space:nowrap}
  .contact svg{flex:none}
</style>
</head>
<body>

<section class="card card--front" aria-label="Card front">
  <div class="wordmark"><span class="wordmark__square"></span>Brisk Coatings</div>
  <p class="front-url">www.<span class="front-url__name">briskcoatingstn</span>.com</p>
</section>

<section class="card card--back" aria-label="Card back">
  <div class="wordmark"><span class="wordmark__square"></span>Brisk Coatings</div>

  <div class="owner">
    <p class="owner__name">Marco "MJ"</p>
    <p class="owner__role">Owner - Licensed &amp; Insured</p>
  </div>

  <svg class="sweep" width="640" height="366" viewBox="0 0 640 366" aria-hidden="true">
    <path d="M40 212 H520 Q575 212 600 196" fill="none" stroke="var(--ink)" stroke-width="2"/>
  </svg>

  <div class="contacts">
    <span class="contact">
      <svg width="14" height="14" viewBox="0 0 24 24"><path fill="var(--accent)" d="M6.6 10.8a15 15 0 0 0 6.6 6.6l2.2-2.2c.3-.3.7-.4 1-.2 1.1.4 2.3.6 3.6.6.6 0 1 .4 1 1V20c0 .6-.4 1-1 1A17 17 0 0 1 3 4c0-.6.4-1 1-1h3.5c.6 0 1 .4 1 1 0 1.3.2 2.5.6 3.6.1.3 0 .7-.2 1z"/></svg>
      555-014-2297
    </span>
    <span class="contact">
      <svg width="15" height="12" viewBox="0 0 24 18"><rect x="1" y="1" width="22" height="16" rx="1" fill="var(--accent)"/><path d="M1 2l11 8 11-8" fill="none" stroke="var(--card)" stroke-width="2"/></svg>
      briskcoatingstn@mail.com
    </span>
    <span class="contact">
      <svg width="14" height="14" viewBox="0 0 24 24"><circle cx="12" cy="12" r="10" fill="var(--accent)"/><path d="M2 12h20M12 2c3 3 3 17 0 20M12 2c-3 3-3 17 0 20" fill="none" stroke="var(--card)" stroke-width="1.5"/></svg>
      briskcoatingstn.com
    </span>
  </div>
</section>

</body>
</html>
```